Keystone Trench Co Business Card*

Looking for a professional, clean and crisp business card

I am in the underground utilities industry and am just looking for a really impressive business card. I would like our card to be white with our symbol crisp and clear with it protruding. I also have a business partner that will require his name and info on the card once the design is set. I would like to have our website info on the card which is;
http://keystonetrenchco.example/

Contact Information for Business Card

Website, contact name, number and email

```html
<!DOCTYPE html>
<html lang="en">
<head>
<meta charset="utf-8">
<title>Keystone Trench Co Business Card</title>
<link rel="stylesheet" href="https://fonts.googleapis.com/css2?family=Oswald:wght@400;500;600&display=swap">
<style>
  :root {
    --backdrop: #b9bfc2;
    --card: #f7f7f5;
    --ink: #2b2b2b;
    --detail: #4d4d4d;
    --name-blue: #3b5fb0;
    --title-red: #e1262b;
    --rule: #3a3a3a;
  }
  * { margin: 0; padding: 0; box-sizing: border-box; }
  html, body {
    width: 1200px;
    height: 824px;
    overflow: hidden;
    background: var(--backdrop);
  }
  .card {
    position: absolute;
    left: 75px;
    top: 112px;
    width: 1050px;
    height: 600px;
    background: var(--card);
    box-shadow: 0 2px 6px rgba(0,0,0,0.12);
    display: flex;
    align-items: center;
    font-family: 'Oswald', sans-serif;
  }
  .brand {
    width: 480px;
    display: flex;
    align-items: center;
    justify-content: center;
    gap: 18px;
  }
  .brand-dot {
    width: 34px;
    height: 34px;
    border-radius: 50%;
    background: var(--ink);
    flex: none;
  }
  .brand-name {
    font-weight: 600;
    font-size: 46px;
    line-height: 1.05;
    color: var(--ink);
    text-transform: uppercase;
    letter-spacing: 1px;
  }
  .divider {
    width: 1.5px;
    height: 330px;
    background: var(--rule);
  }
  .contact {
    padding-left: 48px;
    text-transform: uppercase;
  }
  .contact-name {
    font-weight: 600;
    font-size: 52px;
    line-height: 1;
    color: var(--name-blue);
    letter-spacing: 0.5px;
  }
  .contact-title {
    font-weight: 600;
    font-size: 28px;
    line-height: 1.1;
    color: var(--title-red);
    margin-left: 40px;
    margin-bottom: 22px;
  }
  .contact-lines {
    margin-left: 40px;
    font-weight: 500;
    font-size: 23px;
    line-height: 1.3;
    color: var(--detail);
    letter-spacing: 0.5px;
  }
  .contact-lines + .contact-lines { margin-top: 24px; }
</style>
</head>
<body>
  <main class="card">
    <section class="brand">
      <span class="brand-dot"></span>
      <span class="brand-name">Keystone<br>Trench Co</span>
    </section>
    <div class="divider"></div>
    <section class="contact">
      <h1 class="contact-name">Daniel Reyes</h1>
      <p class="contact-title">President</p>
      <p class="contact-lines">
        Keystone Trench Co LLC<br>
        4120 Birchwood Road<br>
        Fairbanks, Alaska 99701
      </p>
      <p class="contact-lines">
        555-214-7730<br>
        info@keystonetrenchco.example<br>
        www.keystonetrenchco.example
      </p>
    </section>
  </main>
</body>
</html>
```